Business Cards Design for the electrical wholesaler: clean bold dynamic :)

We need a business card design that would follow our latest brand guidelines. As an electrical wholesaler we want to bring a fresh look and feel into the industry. The design should be clean bold and dynamic. It should come alive with the renewed energy of our green colour. Our grey colour should keep things balanced and complement the notion of maturity and responsibility. We employ Lato as a corporate font however are not bound by this font and we’re open to interpretation here.

Target Market(s)

Electrical contractors

Industry/Entity Type

Business

Contact Information for Business Card

Logo
Name & Surname: Halyna Dorosh
Job Title: Director of Marketing
Email: halya.dorosh@quillmail.example
Cell phone: XXX.XXX.XXXX
Address: 20517 - 87 Ave. Edmonton, AB, Canada. T6K 4N8
Business Phone: 780.555.0184
Website: www.brovix.example

Font styles to use
Other font styles liked:
• Lato

Requirements
Must have
• Logo & website
Nice to have
• Brand elements - some of them you may find in the attached Brand Guidelines (e.g. three lines on the background signifying "W")

```html
<!DOCTYPE html>
<html lang="en">
<head>
<meta charset="utf-8">
<title>Brovix Business Cards</title>
<link rel="stylesheet" href="https://fonts.googleapis.com/css2?family=Lato:wght@300;400;700&display=swap">
<style>
  :root {
    --green: #8dc63f;
    --grey: #4d4d4f;
    --grey-soft: #6b6b6d;
    --rule: #7a7a7c;
    --white: #ffffff;
    --backdrop: #e4e5e7;
  }
  * { box-sizing: border-box; margin: 0; padding: 0; }
  html, body { width: 1200px; height: 1000px; overflow: hidden; }
  body {
    background: var(--backdrop);
    font-family: "Lato", sans-serif;
    color: var(--grey);
    position: relative;
  }
  .card {
    position: absolute;
    width: 510px;
    height: 290px;
    background: var(--white);
    overflow: hidden;
    box-shadow: 0 6px 16px rgba(0,0,0,0.18);
  }
  .card--rounded { border-radius: 28px; }
  .card--front-a { left: 64px; top: 60px; }
  .card--back-a  { left: 64px; top: 428px; }
  .card--front-b { left: 626px; top: 283px; }
  .card--back-b  { left: 626px; top: 639px; }

  .front-wave { position: absolute; inset: 0; width: 100%; height: 100%; }
  .front-wordmark {
    position: absolute;
    left: 0; right: 0; top: 82px;
    text-align: center;
    font-weight: 700;
    font-size: 76px;
    line-height: 1;
    letter-spacing: -1px;
    color: var(--grey);
  }

  .back-wordmark {
    position: absolute;
    right: 30px; top: 26px;
    font-weight: 700;
    font-size: 44px;
    line-height: 1;
    letter-spacing: -0.5px;
    color: var(--grey);
  }
  .person-name {
    position: absolute;
    left: 27px; top: 93px;
    font-size: 26px;
    font-weight: 400;
    color: var(--grey);
  }
  .person-title {
    position: absolute;
    left: 27px; top: 128px; right: 30px;
    display: flex; align-items: flex-end; gap: 8px;
    font-size: 15px;
    font-weight: 400;
    color: var(--grey-soft);
  }
  .person-title::after {
    content: "";
    flex: 1;
    border-bottom: 1.5px solid var(--rule);
    margin-bottom: 3px;
  }
  .address {
    position: absolute;
    right: 30px; top: 150px;
    font-size: 15.5px;
    line-height: 20px;
    text-align: right;
    color: var(--grey-soft);
  }
  .address-line { display: flex; align-items: center; justify-content: flex-end; gap: 8px; }
  .contact-list {
    position: absolute;
    left: 28px; top: 182px;
    list-style: none;
    font-size: 16.5px;
    line-height: 24px;
    color: var(--grey);
  }
  .contact-item { display: flex; align-items: center; gap: 12px; }
  .icon { width: 13px; height: 13px; fill: var(--grey); flex: none; }
  .website {
    position: absolute;
    right: 30px; top: 244px;
    font-size: 14.5px;
    color: var(--grey-soft);
  }
</style>
</head>
<body>

<svg width="0" height="0" style="position:absolute" aria-hidden="true">
  <defs>
    <symbol id="icon-pin" viewBox="0 0 24 24"><path d="M12 1C7.6 1 4 4.5 4 8.9 4 15 12 23 12 23s8-8 8-14.1C20 4.5 16.4 1 12 1zm0 11a3.2 3.2 0 1 1 0-6.4 3.2 3.2 0 0 1 0 6.4z"/></symbol>
    <symbol id="icon-mobile" viewBox="0 0 24 24"><path d="M6.6 10.8c1.4 2.8 3.8 5.1 6.6 6.6l2.2-2.2c.3-.3.7-.4 1-.2 1.1.4 2.3.6 3.6.6.6 0 1 .4 1 1V20c0 .6-.4 1-1 1C10.6 21 3 13.4 3 4c0-.6.4-1 1-1h3.5c.6 0 1 .4 1 1 0 1.3.2 2.5.6 3.6.1.3 0 .7-.2 1l-2.3 2.2z"/></symbol>
    <symbol id="icon-desk" viewBox="0 0 24 24"><path d="M12 5C6 5 1.5 7 1 9.5V12h5V9.5c1.8-.6 3.8-.9 6-.9s4.2.3 6 .9V12h5V9.5C22.5 7 18 5 12 5zM6 13l-3 8h18l-3-8h-3v-2h-6v2H6zm6 2a2.5 2.5 0 1 1 0 5 2.5 2.5 0 0 1 0-5z"/></symbol>
    <symbol id="icon-mail" viewBox="0 0 24 24"><path d="M2 5h20v14H2V5zm2 2v.4l8 5.2 8-5.2V7H4z"/></symbol>
    <symbol id="front-wave" viewBox="0 0 510 290" preserveAspectRatio="none"><rect width="510" height="290" fill="#8dc63f"/><path d="M0 245 C60 275 130 272 230 243 S420 188 510 205 L510 290 L0 290 Z" fill="#ffffff"/></symbol>
  </defs>
</svg>

<section class="card card--rounded card--front-a" aria-label="Card front">
  <svg class="front-wave" aria-hidden="true"><use href="#front-wave"/></svg>
  <div class="front-wordmark">brovix</div>
</section>

<section class="card card--rounded card--back-a" aria-label="Card back">
  <div class="back-wordmark">brovix</div>
  <div class="person-name">Halyna Dorosh</div>
  <div class="person-title">Director of Marketing</div>
  <div class="address">
    <div class="address-line"><svg class="icon"><use href="#icon-pin"/></svg>20517 - 87 Ave. Edmonton</div>
    <div class="address-line">AB, Canada. T6K 4N8</div>
  </div>
  <ul class="contact-list">
    <li class="contact-item"><svg class="icon"><use href="#icon-mobile"/></svg>780.555.0184</li>
    <li class="contact-item"><svg class="icon"><use href="#icon-desk"/></svg>780.555.0184</li>
    <li class="contact-item"><svg class="icon"><use href="#icon-mail"/></svg>halya.dorosh@quillmail.example</li>
  </ul>
  <div class="website">www.brovix.example</div>
</section>

<section class="card card--front-b" aria-label="Card front">
  <svg class="front-wave" aria-hidden="true"><use href="#front-wave"/></svg>
  <div class="front-wordmark">brovix</div>
</section>

<section class="card card--back-b" aria-label="Card back">
  <div class="back-wordmark">brovix</div>
  <div class="person-name">Halyna Dorosh</div>
  <div class="person-title">Director of Marketing</div>
  <div class="address">
    <div class="address-line"><svg class="icon"><use href="#icon-pin"/></svg>20517 - 87 Ave. Edmonton</div>
    <div class="address-line">AB, Canada. T6K 4N8</div>
  </div>
  <ul class="contact-list">
    <li class="contact-item"><svg class="icon"><use href="#icon-mobile"/></svg>780.555.0184</li>
    <li class="contact-item"><svg class="icon"><use href="#icon-desk"/></svg>780.555.0184</li>
    <li class="contact-item"><svg class="icon"><use href="#icon-mail"/></svg>halya.dorosh@quillmail.example</li>
  </ul>
  <div class="website">www.brovix.example</div>
</section>

</body>
</html>
```